TL - business card

Tallow Partners is an insurance brokerage firm, inovative, proactive, vigorous, which aims to become the leader of the insurance brokers in Anfrica. We should like to get some designs which should be avoided also in Gray / Metallic for the Administration and Orange / Blue for the Managers (ike in the picture sent). The Blue / Green logo is not the correct one, but the source of the file. Please adjust the color accordingly for the business cards. 1 / Orange / Blue 2 / Gray / Metallic We want something classic but which is transmitted strenght, inovation, modernity and most of all, rapidity. We want something start-up like, very punchy and catching eye remaining profesional at the same time. Name: Dorian Whitlock Function: Managing Director Address: N ° 17/18 Rua Veloso - R / C 2B Direita - Bairro Mutamba - Luanda Tel: (+244) 947 582 316 Email: dorian.whitlock@tallow-p.example Website: www.tallow-p. example We want classic in the front and creative, colorfull at the back. The cards will be printed in relief, with very high quality of paper.
Insurance Broker
Colors
Designer to choose colors to be used in the design.

```html
<!DOCTYPE html>
<html lang="en">
<head>
<meta charset="utf-8">
<title>TL - business card</title>
<link rel="stylesheet" href="https://fonts.googleapis.com/css2?family=Roboto:wght@400;500;700&display=swap">
<style>
  :root {
    --sky: #29a9e0;
    --leaf: #009444;
    --paper: #ffffff;
    --backdrop: #2a2a2a;
  }
  * { margin: 0; padding: 0; box-sizing: border-box; }
  html, body {
    width: 1200px; height: 960px; overflow: hidden;
    background: var(--backdrop);
    font-family: "Roboto", Arial, sans-serif;
  }
  .sheet {
    width: 1200px; height: 960px;
    display: flex; flex-direction: column; align-items: center; justify-content: center;
    gap: 40px;
  }
  .card {
    position: relative;
    width: 700px; height: 400px;
    overflow: hidden;
    box-shadow: 0 10px 30px rgba(0,0,0,.5);
  }
  .card-art { position: absolute; inset: 0; }

  /* front */
  .holder { position: absolute; left: 52px; top: 54px; color: var(--paper); }
  .holder-name { font-size: 30px; font-weight: 700; line-height: 1.1; }
  .holder-role { font-size: 17px; font-weight: 500; margin-top: 2px; }
  .address {
    position: absolute; left: 72px; top: 200px;
    color: var(--paper); font-size: 17px; line-height: 1.3;
  }
  .contacts {
    position: absolute; left: 72px; top: 282px;
    list-style: none; color: var(--paper); font-size: 17px; line-height: 1.5;
  }
  .contacts li { display: flex; align-items: center; gap: 10px; }
  .contacts svg { width: 16px; height: 16px; flex: none; }
  .brand {
    position: absolute; left: 420px; top: 150px; width: 260px;
    display: flex; flex-direction: column; align-items: center; gap: 14px;
  }
  .brand-dot { width: 54px; height: 54px; border-radius: 50%; background: var(--sky); }
  .brand-name { color: var(--leaf); font-size: 30px; font-weight: 700; letter-spacing: .5px; white-space: nowrap; }

  /* back */
  .card-back { background: var(--sky); }
  .back-brand {
    position: absolute; inset: 0;
    display: flex; flex-direction: column; align-items: center; justify-content: center; gap: 18px;
  }
  .back-dot { width: 120px; height: 120px; border-radius: 50%; border: 10px solid var(--leaf); }
  .back-name { color: var(--paper); font-size: 34px; font-weight: 700; }
  .back-web { color: var(--paper); font-size: 16px; letter-spacing: 6px; }
</style>
</head>
<body>
<main class="sheet">

  <section class="card card-front" aria-label="Card front">
    <svg class="card-art" viewBox="0 0 700 400" aria-hidden="true">
      <rect width="700" height="400" fill="var(--sky)"/>
      <path d="M458 0 C380 60 345 170 372 260 C390 320 430 370 470 400 L700 400 L700 0 Z" fill="var(--leaf)"/>
      <path d="M470 28 L478 0 L700 0 L700 400 L490 400 C440 360 405 310 395 250 C382 160 415 80 470 28 Z" fill="var(--paper)"/>
    </svg>
    <div class="holder">
      <p class="holder-name">Dorian Whitlock</p>
      <p class="holder-role">Managing Director</p>
    </div>
    <address class="address">
      N ° 17/18 Rua Veloso<br>
      R / C 2B Direita<br>
      Bairro Mutamba, Luanda
    </address>
    <ul class="contacts">
      <li>
        <svg viewBox="0 0 16 16" aria-hidden="true"><path fill="#fff" d="M3 1l3 0 1 4-2 1.5c1 2 2.5 3.5 4.5 4.5L11 9l4 1v3c0 1-1 2-2 2C6.5 15 1 9.5 1 3c0-1 1-2 2-2z"/></svg>
        (+244) 947 582 316
      </li>
      <li>
        <svg viewBox="0 0 16 16" aria-hidden="true"><rect x="1" y="3" width="14" height="10" fill="#fff"/><path d="M1 3l7 6 7-6" fill="none" stroke="var(--sky)" stroke-width="1.5"/></svg>
        dorian.whitlock@tallow-p.example
      </li>
      <li>
        <svg viewBox="0 0 16 16" aria-hidden="true"><circle cx="8" cy="8" r="7" fill="#fff"/><path d="M1 8h14M8 1c-3 4-3 10 0 14M8 1c3 4 3 10 0 14" fill="none" stroke="var(--sky)" stroke-width="1"/></svg>
        www.tallow-p. example
      </li>
    </ul>
    <div class="brand">
      <span class="brand-dot" aria-hidden="true"></span>
      <span class="brand-name">Tallow Partners</span>
    </div>
  </section>

  <section class="card card-back" aria-label="Card back">
    <div class="back-brand">
      <span class="back-dot" aria-hidden="true"></span>
      <span class="back-name">Tallow Partners</span>
      <span class="back-web">www.tallow-p. example</span>
    </div>
  </section>

</main>
</body>
</html>
```